MES Modul-Struktur grafisch veranschaulichen
Zielgruppe
Wir sind Software-Hersteller. Thema 'MES'. Unsere Kunden sind Produktionsunternehmen.
Mit einem MES (Manufacturing Execution System) werden Produktionsprozesse überwacht, geplant, gesteuert und optimiert. Allgemein geht es darum, die Produktivität zu steigern und Kosten zu minimieren.
Eine MES-Software ist modular strukturiert, so dass der Kunde sich nach Bedarf die einzelnen Funktionsmodule zusammenstellen kann. Unser MES KORVIN 7 MAX besteht z.B. aus folgenden Einzelmodulen:
- BASIS (Basismodul)
- MDE (Maschinendatenerfassung)
- BDE (Betriebsdatenerfassung)
- INST (Instandhaltung)
- ALARM (Alarmierung)
- DOK (Dokumentenmanagement)
- TNT (Traceability)
- PLAN (Feinplanung/Leitstand)
- LOG (Logistik)
- VIS (Visualisierung)
- PEP (Personaleinsatzplanung)
- MPZE (Personalzeiterfassung)
- DNC (Rezepturen/DNC)
- EM (Energiemonitoring)
Aufgabenstellung
Die modulare Struktur und der große Umfang an Modulen ist ein wichtiger Vorteil für unsere Kunden, da Sie nicht so schnell an Grenzen stoßen und sich dann unter Umständen eine weitere Insellösung (extra Software mit extra Datenbank ...) anschaffen müssen.
Wichtig ist, dass die einzelnen Module funktionell ineinandergreifen und alle auf die gleiche Datenbank zugreifen.
Es reicht wenn in der Grafik die Module nur mit er Abkürzung, also z.B. MDE bezeichnet werden. Für den ersten Entwurf können auch Platzhalter genutzt werden.
Der Betrachter sollte aus der Grafik auf den ersten Blick erkennen:
- umfängliches MES
- modular strukturiert
- Funktionsmodule step-by-step erweiterbar
Für die Umsetzung naheliegend wären Puzzle-Steine, Blokkis, ... muss aber nicht.

```html
<!DOCTYPE html>
<html lang="de">
<head>
<meta charset="utf-8">
<title>MES Modul-Struktur</title>
<link rel="stylesheet" href="https://fonts.googleapis.com/css2?family=Source+Sans+3:wght@400;600;700&display=swap">
<style>
  :root {
    --bg: #e2e5e8;
    --spine: #c7d1db;
    --white: #ffffff;
    --shadow: rgba(40, 50, 60, 0.28);
    --em-light: #6b3f8e;   --em-dark: #4a2a6d;
    --dnc-light: #8c4b91;  --dnc-dark: #6c2e72;
    --mpze-light: #2e70b8; --mpze-dark: #15549e;
    --pep-light: #62acde;  --pep-dark: #2f8ece;
    --vis-light: #98d2f1;  --vis-dark: #6dbce8;
    --log-light: #2f6a40;  --log-dark: #0e4d2a;
    --plan-light: #2a7c48; --plan-dark: #0e6034;
    --tnt-light: #3fa858;  --tnt-dark: #13903a;
    --dok-light: #80bd49;  --dok-dark: #63a830;
    --alarm-light: #c9d84c; --alarm-dark: #adc31c;
    --inst-light: #ee6e3b; --inst-dark: #e04c1a;
    --bde-light: #f6a551;  --bde-dark: #ee8613;
    --mde-light: #fcc647;  --mde-dark: #f6ac10;
    --basis-light: #d0d8e0; --basis-dark: #b7c3cf;
  }
  * { box-sizing: border-box; margin: 0; padding: 0; }
  html, body { width: 848px; height: 1200px; overflow: hidden; background: var(--bg); }
  body { position: relative; font-family: "Source Sans 3", "Myriad Pro", Arial, sans-serif; color: var(--white); }

  .spine { position: absolute; left: 419px; top: 0; width: 11px; height: 1200px; background: var(--spine); }

  .node {
    position: absolute; left: 406px; width: 36px; height: 36px; border-radius: 50%;
    background: var(--white); box-shadow: 0 1px 4px var(--shadow);
  }
  .node::after {
    content: ""; position: absolute; left: 6px; top: 6px; width: 24px; height: 24px;
    border-radius: 50%; background: var(--dot);
  }

  .module { position: absolute; height: 88px; }
  .module--left { left: 153px; width: 207px; }
  .module--right { left: 480px; width: 215px; }

  .module__tag { position: absolute; top: 0; width: 200px; height: 88px; filter: drop-shadow(0 2px 3px var(--shadow)); }
  .module--left .module__tag { left: 7px; }
  .module--right .module__tag { left: 0; }
  .tag-frame { fill: var(--white); }
  .tag-top { fill: var(--light); }
  .tag-bottom { fill: var(--dark); }

  .module__badge {
    position: absolute; top: -3px; width: 94px; height: 94px; border-radius: 50%;
    background: var(--white); box-shadow: 0 2px 5px var(--shadow);
    display: flex; align-items: center; justify-content: center;
  }
  .module--left .module__badge { left: 0; }
  .module--right .module__badge { left: 121px; }
  .badge-core {
    width: 78px; height: 78px; border-radius: 50%;
    background: linear-gradient(var(--light), var(--dark));
    display: flex; align-items: center; justify-content: center;
  }
  .badge-core svg { width: 40px; height: 40px; fill: none; stroke: var(--white); stroke-width: 2.6; stroke-linecap: round; stroke-linejoin: round; }
  .badge-core .solid { fill: var(--white); stroke: none; }

  .module__text { position: absolute; top: 0; height: 88px; }
  .module--left .module__text { left: 97px; text-align: left; }
  .module--right .module__text { right: 101px; text-align: right; }
  .module__code { position: absolute; top: 10px; font-size: 24px; font-weight: 700; line-height: 1; letter-spacing: 0.3px; white-space: nowrap; }
  .module__name { position: absolute; top: 51px; font-size: 11.5px; font-weight: 600; line-height: 1.2; white-space: nowrap; }
  .module--left .module__code, .module--left .module__name { left: 0; }
  .module--right .module__code, .module--right .module__name { right: 0; }
</style>
</head>
<body>
  <div class="spine"></div>

  <div class="node" style="top:77px;--dot:var(--em-dark)"></div>
  <div class="node" style="top:152px;--dot:var(--dnc-dark)"></div>
  <div class="node" style="top:226px;--dot:var(--mpze-dark)"></div>
  <div class="node" style="top:301px;--dot:var(--pep-dark)"></div>
  <div class="node" style="top:375px;--dot:var(--vis-dark)"></div>
  <div class="node" style="top:450px;--dot:var(--log-dark)"></div>
  <div class="node" style="top:525px;--dot:var(--plan-dark)"></div>
  <div class="node" style="top:599px;--dot:var(--tnt-dark)"></div>
  <div class="node" style="top:674px;--dot:var(--dok-dark)"></div>
  <div class="node" style="top:748px;--dot:var(--alarm-dark)"></div>
  <div class="node" style="top:823px;--dot:var(--inst-dark)"></div>
  <div class="node" style="top:897px;--dot:var(--bde-dark)"></div>
  <div class="node" style="top:972px;--dot:var(--mde-dark)"></div>
  <div class="node" style="top:1046px;--dot:var(--basis-dark)"></div>

  <!-- Left column -->
  <article class="module module--left" style="top:49px;--light:var(--em-light);--dark:var(--em-dark)">
    <svg class="module__tag" viewBox="0 0 200 88"><polygon class="tag-frame" points="0,0 182,0 200,44 182,88 0,88"/><polygon class="tag-top" points="5,5 179,5 194,44 5,44"/><polygon class="tag-bottom" points="5,44 194,44 179,83 5,83"/></svg>
    <div class="module__text"><h2 class="module__code">EM</h2><p class="module__name">Energie-<br>monitoring</p></div>
    <div class="module__badge"><div class="badge-core"><svg viewBox="0 0 40 40"><rect x="5" y="12" width="27" height="16" rx="2"/><rect class="solid" x="33" y="17" width="3" height="6"/><rect class="solid" x="9" y="16" width="9" height="8"/></svg></div></div>
  </article>

  <article class="module module--left" style="top:198px;--light:var(--mpze-light);--dark:var(--mpze-dark)">
    <svg class="module__tag" viewBox="0 0 200 88"><polygon class="tag-frame" points="0,0 182,0 200,44 182,88 0,88"/><polygon class="tag-top" points="5,5 179,5 194,44 5,44"/><polygon class="tag-bottom" points="5,44 194,44 179,83 5,83"/></svg>
    <div class="module__text"><h2 class="module__code">MPZE</h2><p class="module__name">Personalzeit-<br>erfassung</p></div>
    <div class="module__badge"><div class="badge-core"><svg viewBox="0 0 40 40"><circle cx="20" cy="21" r="13"/><path d="M20 13v8l6 4M14 5h12"/></svg></div></div>
  </article>

  <article class="module module--left" style="top:348px;--light:var(--vis-light);--dark:var(--vis-dark)">
    <svg class="module__tag" viewBox="0 0 200 88"><polygon class="tag-frame" points="0,0 182,0 200,44 182,88 0,88"/><polygon class="tag-top" points="5,5 179,5 194,44 5,44"/><polygon class="tag-bottom" points="5,44 194,44 179,83 5,83"/></svg>
    <div class="module__text"><h2 class="module__code">VIS</h2><p class="module__name">Visualisierung</p></div>
    <div class="module__badge"><div class="badge-core"><svg viewBox="0 0 40 40"><path d="M4 20c5-8 11-11 16-11s11 3 16 11c-5 8-11 11-16 11S9 28 4 20z"/><circle class="solid" cx="20" cy="20" r="5"/></svg></div></div>
  </article>

  <article class="module module--left" style="top:498px;--light:var(--plan-light);--dark:var(--plan-dark)">
    <svg class="module__tag" viewBox="0 0 200 88"><polygon class="tag-frame" points="0,0 182,0 200,44 182,88 0,88"/><polygon class="tag-top" points="5,5 179,5 194,44 5,44"/><polygon class="tag-bottom" points="5,44 194,44 179,83 5,83"/></svg>
    <div class="module__text"><h2 class="module__code">PLAN</h2><p class="module__name">Feinplanung/<br>Leitstand</p></div>
    <div class="module__badge"><div class="badge-core"><svg viewBox="0 0 40 40"><rect x="6" y="9" width="28" height="25" rx="2"/><path d="M6 16h28M13 5v7M27 5v7M12 22h4M18 22h4M24 22h4M12 28h4M18 28h4"/></svg></div></div>
  </article>

  <article class="module module--left" style="top:648px;--light:var(--dok-light);--dark:var(--dok-dark)">
    <svg class="module__tag" viewBox="0 0 200 88"><polygon class="tag-frame" points="0,0 182,0 200,44 182,88 0,88"/><polygon class="tag-top" points="5,5 179,5 194,44 5,44"/><polygon class="tag-bottom" points="5,44 194,44 179,83 5,83"/></svg>
    <div class="module__text"><h2 class="module__code">DOK</h2><p class="module__name">Dokumenten-<br>management</p></div>
    <div class="module__badge"><div class="badge-core"><svg viewBox="0 0 40 40"><path d="M9 4h15l7 7v25H9z"/><path d="M24 4v7h7M14 17h12M14 22h12M14 27h12"/></svg></div></div>
  </article>

  <article class="module module--left" style="top:797px;--light:var(--inst-light);--dark:var(--inst-dark)">
    <svg class="module__tag" viewBox="0 0 200 88"><polygon class="tag-frame" points="0,0 182,0 200,44 182,88 0,88"/><polygon class="tag-top" points="5,5 179,5 194,44 5,44"/><polygon class="tag-bottom" points="5,44 194,44 179,83 5,83"/></svg>
    <div class="module__text"><h2 class="module__code">INST</h2><p class="module__name">Instandhaltung</p></div>
    <div class="module__badge"><div class="badge-core"><svg viewBox="0 0 40 40"><path d="M9 31L27 13M26 7a6 6 0 0 0 7 7M31 31L13 13M7 9l4-4 4 4-4 4z" stroke-width="4"/></svg></div></div>
  </article>

  <article class="module module--left" style="top:949px;--light:var(--mde-light);--dark:var(--mde-dark)">
    <svg class="module__tag" viewBox="0 0 200 88"><polygon class="tag-frame" points="0,0 182,0 200,44 182,88 0,88"/><polygon class="tag-top" points="5,5 179,5 194,44 5,44"/><polygon class="tag-bottom" points="5,44 194,44 179,83 5,83"/></svg>
    <div class="module__text"><h2 class="module__code">MDE</h2><p class="module__name">Maschinendaten-<br>erfassung</p></div>
    <div class="module__badge"><div class="badge-core"><svg viewBox="0 0 40 40"><circle cx="14" cy="15" r="7" stroke-dasharray="3 2.5" stroke-width="5"/><circle cx="14" cy="15" r="2.5"/><circle cx="16" cy="29" r="5" stroke-dasharray="2.5 2" stroke-width="4"/><path d="M24 32L34 8"/></svg></div></div>
  </article>

  <!-- Right column -->
  <article class="module module--right" style="top:128px;--light:var(--dnc-light);--dark:var(--dnc-dark)">
    <svg class="module__tag" viewBox="0 0 200 88"><polygon class="tag-frame" points="0,44 18,0 200,0 200,88 18,88"/><polygon class="tag-top" points="6,44 21,5 195,5 195,44"/><polygon class="tag-bottom" points="6,44 195,44 195,83 21,83"/></svg>
    <div class="module__text"><h2 class="module__code">DNC</h2><p class="module__name">Rezepturen/DNC</p></div>
    <div class="module__badge"><div class="badge-core"><svg viewBox="0 0 40 40"><rect class="solid" x="15" y="5" width="10" height="8"/><rect class="solid" x="4" y="27" width="9" height="8"/><rect class="solid" x="15.5" y="27" width="9" height="8"/><rect class="solid" x="27" y="27" width="9" height="8"/><path d="M20 13v14M8.5 27v-7h23v7"/></svg></div></div>
  </article>

  <article class="module module--right" style="top:272px;--light:var(--pep-light);--dark:var(--pep-dark)">
    <svg class="module__tag" viewBox="0 0 200 88"><polygon class="tag-frame" points="0,44 18,0 200,0 200,88 18,88"/><polygon class="tag-top" points="6,44 21,5 195,5 195,44"/><polygon class="tag-bottom" points="6,44 195,44 195,83 21,83"/></svg>
    <div class="module__text"><h2 class="module__code">PEP</h2><p class="module__name">Personaleinsatz-<br>planung</p></div>
    <div class="module__badge"><div class="badge-core"><svg viewBox="0 0 40 40"><circle class="solid" cx="20" cy="10" r="4.5"/><circle class="solid" cx="9" cy="13" r="3.5"/><circle class="solid" cx="31" cy="13" r="3.5"/><path class="solid" d="M14 17h12v12h-3v6h-6v-6h-3zM4 19h8v9H10v5H6v-5H4zM28 19h8v9h-2v5h-4v-5h-2z"/></svg></div></div>
  </article>

  <article class="module module--right" style="top:422px;--light:var(--log-light);--dark:var(--log-dark)">
    <svg class="module__tag" viewBox="0 0 200 88"><polygon class="tag-frame" points="0,44 18,0 200,0 200,88 18,88"/><polygon class="tag-top" points="6,44 21,5 195,5 195,44"/><polygon class="tag-bottom" points="6,44 195,44 195,83 21,83"/></svg>
    <div class="module__text"><h2 class="module__code">LOG</h2><p class="module__name">Logistik</p></div>
    <div class="module__badge"><div class="badge-core"><svg viewBox="0 0 40 40"><path class="solid" d="M3 11h22v16H3zM26 15h6l5 6v6H26z"/><circle class="solid" cx="10" cy="30" r="3.5"/><circle class="solid" cx="30" cy="30" r="3.5"/></svg></div></div>
  </article>

  <article class="module module--right" style="top:572px;--light:var(--tnt-light);--dark:var(--tnt-dark)">
    <svg class="module__tag" viewBox="0 0 200 88"><polygon class="tag-frame" points="0,44 18,0 200,0 200,88 18,88"/><polygon class="tag-top" points="6,44 21,5 195,5 195,44"/><polygon class="tag-bottom" points="6,44 195,44 195,83 21,83"/></svg>
    <div class="module__text"><h2 class="module__code">TNT</h2><p class="module__name">Traceability</p></div>
    <div class="module__badge"><div class="badge-core"><svg viewBox="0 0 40 40"><path d="M4 12h8c8 0 10 16 18 16h4M4 28h8c3 0 5-2 7-5M22 17c2-3 4-5 8-5h4M30 7l5 5-5 5M30 23l5 5-5 5" stroke-width="3"/></svg></div></div>
  </article>

  <article class="module module--right" style="top:720px;--light:var(--alarm-light);--dark:var(--alarm-dark)">
    <svg class="module__tag" viewBox="0 0 200 88"><polygon class="tag-frame" points="0,44 18,0 200,0 200,88 18,88"/><polygon class="tag-top" points="6,44 21,5 195,5 195,44"/><polygon class="tag-bottom" points="6,44 195,44 195,83 21,83"/></svg>
    <div class="module__text"><h2 class="module__code">ALARM</h2><p class="module__name">Alarmierung</p></div>
    <div class="module__badge"><div class="badge-core"><svg viewBox="0 0 40 40"><circle class="solid" cx="20" cy="20" r="4"/><path d="M14 14a8 8 0 0 0 0 12M26 14a8 8 0 0 1 0 12M9 9a15 15 0 0 0 0 22M31 9a15 15 0 0 1 0 22"/></svg></div></div>
  </article>

  <article class="module module--right" style="top:871px;--light:var(--bde-light);--dark:var(--bde-dark)">
    <svg class="module__tag" viewBox="0 0 200 88"><polygon class="tag-frame" points="0,44 18,0 200,0 200,88 18,88"/><polygon class="tag-top" points="6,44 21,5 195,5 195,44"/><polygon class="tag-bottom" points="6,44 195,44 195,83 21,83"/></svg>
    <div class="module__text"><h2 class="module__code">BDE</h2><p class="module__name">Betriebsdaten-<br>erfassung</p></div>
    <div class="module__badge"><div class="badge-core"><svg viewBox="0 0 40 40"><path d="M6 6v28h28M12 30V20M18 30V14M24 30V22M30 30V17"/><circle cx="22" cy="15" r="5"/></svg></div></div>
  </article>

  <article class="module module--right" style="top:1020px;--light:var(--basis-light);--dark:var(--basis-dark)">
    <svg class="module__tag" viewBox="0 0 200 88"><polygon class="tag-frame" points="0,44 18,0 200,0 200,88 18,88"/><polygon class="tag-top" points="6,44 21,5 195,5 195,44"/><polygon class="tag-bottom" points="6,44 195,44 195,83 21,83"/></svg>
    <div class="module__text"><h2 class="module__code">BASIS</h2><p class="module__name">Basismodul</p></div>
    <div class="module__badge"><div class="badge-core"><svg viewBox="0 0 40 40"><path d="M20 35S9 23 9 15a11 11 0 0 1 22 0c0 8-11 20-11 20z"/><circle cx="20" cy="15" r="4"/></svg></div></div>
  </article>
</body>
</html>
```